Letterhead and matching envelope design for a dental office

We need a new stationary design, letterhead and envelope #10, for a dental office in Denver area. We are called Bright Harbor Dental. We want a simple and minimalistic design but not a boring design. I wish to have one good point that makes it look professional. I have attached our logo. Feel free to use either one. I want the design for letterhead and envelope look like a "matching pair" but not look the same. The envelope doesn't have to be white and it will have an address window on bottom left.

Target Market(s)

everyone who visits dentist (adults)

Industry/Entity Type

Dental

Font styles to use
Other font styles liked:
• close to font on logo or something that matches well

Requirements
Must have
• professional
• simple, minimalistic
• unique point that stands out
Nice to have
• matching but not same design for letterhead and envelope
Should not have
• not look like all the other boring designs
• no flowery, distracting feats

```html
<!DOCTYPE html>
<html lang="en">
<head>
<meta charset="utf-8">
<title>Bright Harbor Dental – #10 Envelope</title>
<link rel="stylesheet" href="https://fonts.googleapis.com/css2?family=Source+Sans+3:wght@400;600&display=swap">
<style>
  :root {
    --page-bg: #e9ebe8;
    --brand-green: #39b54a;
    --soft-green: #b7dfb9;
    --faint-green: #eef6ee;
    --paper: #ffffff;
    --ink-white: #ffffff;
  }
  html, body {
    margin: 0;
    padding: 0;
    width: 1200px;
    height: 800px;
    overflow: hidden;
    background: var(--page-bg);
  }
  .canvas {
    position: relative;
    width: 1200px;
    height: 800px;
    font-family: "Source Sans 3", "Myriad Pro", Arial, sans-serif;
  }
  .envelope-art {
    position: absolute;
    inset: 0;
  }
  .flap-name, .front-name {
    position: absolute;
    margin: 0;
    text-align: center;
    text-transform: uppercase;
    font-weight: 600;
    line-height: 1.15;
  }
  .flap-name {
    left: 500px;
    top: 180px;
    width: 200px;
    font-size: 15px;
    letter-spacing: 3px;
    color: var(--ink-white);
  }
  .front-name {
    left: 480px;
    top: 330px;
    width: 240px;
    font-size: 21px;
    letter-spacing: 4px;
    color: var(--brand-green);
  }
  .contact-list {
    position: absolute;
    right: 190px;
    top: 592px;
    margin: 0;
    padding: 0;
    list-style: none;
    text-align: right;
    white-space: nowrap;
    color: var(--ink-white);
    font-size: 15.5px;
    line-height: 22.3px;
  }
</style>
</head>
<body>
<main class="canvas">
  <svg class="envelope-art" width="1200" height="800" viewBox="0 0 1200 800">
    <path class="envelope-flap" fill="var(--brand-green)"
      d="M125 277 L152 170 Q158 146 182 140 L600 112 L1018 140 Q1042 146 1048 170 L1075 277 Z"/>
    <rect class="envelope-body" x="125" y="277" width="950" height="413" fill="var(--paper)"/>
    <rect role="img" aria-label="Faint large leaf motif area" x="160" y="330" width="420" height="340" rx="120" fill="var(--faint-green)" opacity="0.6"/>
    <path class="wave-soft" fill="var(--soft-green)"
      d="M125 628 C300 680 420 650 620 600 C800 555 950 520 1075 515 L1075 690 L125 690 Z"/>
    <path class="wave-line" fill="none" stroke="var(--paper)" stroke-width="4"
      d="M125 634 C300 688 430 660 630 610 C810 568 950 540 1075 534"/>
    <path class="wave-main" fill="var(--brand-green)"
      d="M125 640 C300 700 440 672 640 622 C820 580 950 560 1075 556 L1075 690 L125 690 Z"/>
    <g class="contact-icons" fill="var(--ink-white)">
      <circle cx="1022" cy="603" r="8"/>
      <circle cx="1022" cy="625" r="8"/>
      <circle cx="1022" cy="647" r="8"/>
      <circle cx="1022" cy="670" r="8"/>
    </g>
    <g class="icon-glyphs" fill="none" stroke="var(--brand-green)" stroke-width="1.6" stroke-linecap="round" stroke-linejoin="round">
      <path d="M1019 599 q-1 5 5 8 l1.5 -1.5"/>
      <rect x="1017.5" y="621.5" width="9" height="7" rx="1"/>
      <path d="M1017.5 622 l4.5 3.5 l4.5 -3.5"/>
      <circle cx="1022" cy="647" r="4.5"/>
      <path d="M1017.5 647 h9 M1022 642.5 q-3 4.5 0 9 q3 -4.5 0 -9"/>
      <path d="M1022 675 q-4.5 -4 -4.5 -6.5 a4.5 4.5 0 0 1 9 0 q0 2.5 -4.5 6.5 z"/>
      <circle cx="1022" cy="668.5" r="1.3"/>
    </g>
  </svg>

  <p class="flap-name">Bright Harbor<br>Dental</p>
  <p class="front-name">Bright Harbor<br>Dental</p>

  <ul class="contact-list">
    <li class="contact-phone">720-555-0142</li>
    <li class="contact-email">info@brightharbordental.com</li>
    <li class="contact-web">www.brightharbordental.com</li>
    <li class="contact-address">4821 Linden Ridge Dr,Suite 210 Westminster, CO 80031</li>
  </ul>
</main>
</body>
</html>
```